QVR business card

Need a business card for a company that provides instructional design and elearning development services. The website is here: http://quorvane.studio/

I'm attaching a current logo, as well as the old business card design. While I like to keep it clean, the old design is too simplistic for my liking. The only idea I want to reuse from the old design is placing industry jargon on the back of the card, just need a better way to present it. But if you have other ideas for the back--feel free to experiment.

Please use the colors complementary to the color we have on the website. Thank you!

```html
<!DOCTYPE html>
<html lang="en">
<head>
<meta charset="utf-8">
<title>QVR business card</title>
<link rel="stylesheet" href="https://fonts.googleapis.com/css2?family=Open+Sans:wght@400;600;700;800&family=Fira+Sans+Extra+Condensed:wght@400;500&display=swap">
<style>
  :root {
    --teal: #1bb1ae;
    --teal-dark: #15a09d;
    --khaki: #d9d096;
    --gold: #d7c873;
    --ink: #2b2b2b;
    --paper: #ffffff;
    --backdrop: #ecebe7;
  }
  * { box-sizing: border-box; margin: 0; padding: 0; }
  html, body {
    width: 1200px; height: 675px; overflow: hidden;
    background: var(--backdrop);
    font-family: "Open Sans", Arial, sans-serif;
  }
  .canvas { position: relative; width: 1200px; height: 675px; }

  .card {
    position: absolute; width: 520px; height: 300px;
    border-radius: 24px; overflow: hidden;
    box-shadow: 0 6px 18px rgba(0,0,0,0.12);
  }

  /* Back side */
  .card-back {
    left: 50px; top: 70px;
    background: var(--teal);
    display: flex; align-items: center;
    padding: 0 28px 0 30px;
    color: var(--paper);
  }
  .back-question {
    font-weight: 800; text-transform: uppercase;
    line-height: 0.92; letter-spacing: -1px;
    padding-right: 18px;
    border-right: 2px solid rgba(255,255,255,0.85);
    align-self: stretch;
    display: flex; flex-direction: column; justify-content: center;
  }
  .back-question span { display: block; }
  .back-question .q-sm { font-size: 44px; }
  .back-question .q-lg { font-size: 66px; }
  .back-question .q-md { font-size: 46px; }
  .jargon-list {
    list-style: none; padding-left: 18px;
    font-family: "Fira Sans Extra Condensed", "Arial Narrow", sans-serif;
    font-size: 27px; line-height: 1.2; text-transform: uppercase;
    white-space: nowrap;
  }
  .card-back { padding-top: 26px; padding-bottom: 26px; }

  /* Front side */
  .card-front { left: 630px; top: 305px; background: var(--paper); }
  .front-bands { position: absolute; inset: 0; }
  .brand {
    position: absolute; left: 30px; top: 34px;
    display: flex; align-items: center; gap: 10px;
  }
  .brand-dot { width: 26px; height: 26px; border-radius: 50%; background: var(--teal); }
  .brand-name { font-size: 40px; font-weight: 700; color: var(--gold); letter-spacing: 1px; }

  .contact-list {
    position: absolute; left: 26px; top: 132px;
    list-style: none; font-size: 13px; color: var(--ink);
  }
  .contact-list li { display: flex; align-items: center; gap: 8px; height: 19px; }
  .contact-icon { width: 14px; height: 14px; flex: none; }

  .person {
    position: absolute; right: 24px; top: 152px; text-align: right;
  }
  .person-name { font-size: 15px; font-weight: 700; color: var(--gold); text-transform: uppercase; letter-spacing: 0.3px; }
  .person-role { font-size: 14px; color: var(--ink); margin-top: 1px; }
</style>
</head>
<body>
<main class="canvas">

  <section class="card card-back" aria-label="Card back">
    <h2 class="back-question">
      <span class="q-sm">How</span>
      <span class="q-sm">Can</span>
      <span class="q-lg">We</span>
      <span class="q-md">Help?</span>
    </h2>
    <ul class="jargon-list">
      <li>Mobile Learning SCORM</li>
      <li>Instructional Design LMS</li>
      <li>MOOCs eLearning HTML5</li>
      <li>Adult Learning Theory</li>
      <li>Gamification Classroom</li>
      <li>xAPI Blended Learning</li>
    </ul>
  </section>

  <section class="card card-front" aria-label="Card front">
    <svg class="front-bands" viewBox="0 0 520 300" width="520" height="300" aria-hidden="true">
      <polygon points="0,118 350,118 378,198 520,198 520,300 0,300" fill="var(--khaki)"/>
      <polygon points="0,108 342,108 366,146 520,146 520,198 378,198 350,118 0,118" fill="var(--teal)"/>
    </svg>

    <div class="brand">
      <span class="brand-dot"></span>
      <span class="brand-name">QVR</span>
    </div>

    <ul class="contact-list">
      <li>
        <svg class="contact-icon" viewBox="0 0 14 14"><circle cx="7" cy="7" r="7" fill="var(--teal)"/><path d="M4.5 3.8c.4-.4 1-.4 1.2.1l.5 1.1c.1.3 0 .6-.2.8l-.4.4c.4.9 1.1 1.6 2 2l.4-.4c.2-.2.5-.3.8-.2l1.1.5c.5.2.5.8.1 1.2-.9.9-2.2.6-3.6-.6C5 7.5 3.7 5 4.5 3.8z" fill="#fff"/></svg>
        555-014-2873
      </li>
      <li>
        <svg class="contact-icon" viewBox="0 0 14 14"><circle cx="7" cy="7" r="7" fill="var(--teal)"/><rect x="3.5" y="4.5" width="7" height="5" rx="0.6" fill="#fff"/><path d="M3.7 4.8 7 7.3l3.3-2.5" stroke="var(--teal)" stroke-width="0.8" fill="none"/></svg>
        mdelavine@quorvane.studio
      </li>
      <li>
        <svg class="contact-icon" viewBox="0 0 14 14"><circle cx="7" cy="7" r="7" fill="var(--teal)"/><circle cx="7" cy="7" r="3.6" fill="none" stroke="#fff" stroke-width="0.9"/><ellipse cx="7" cy="7" rx="1.5" ry="3.6" fill="none" stroke="#fff" stroke-width="0.8"/><path d="M3.4 7h7.2" stroke="#fff" stroke-width="0.8"/></svg>
        www.quorvane.studio
      </li>
    </ul>

    <div class="person">
      <p class="person-name">Marcus Delavine</p>
      <p class="person-role">Managing Director</p>
    </div>
  </section>

</main>
</body>
</html>
```